Letter design, envelope design, and more

Hello, we the Tavrin Gmbh are looking for our shop. Letter C5. Design does not have to be like a business card, so it can have straight lines. Only the color is important. The logo is the text under TaVRin omit.It should not be playful but Profesionel

Font styles to use
Sans Serif

Colors
0555a3
3176b5
85abd2
85cae6
34a7d8
0792cd
cee9f5
cfdfed
000000

Requirements
Must have
• Color like business card, Please, with the text under TaVRin, Correct address Lindmattstr. 4 Zip code 9517 Goldach, as well as Couvert Without addressing only design and logo with TaVrn
Nice to have
• more writing articles
Should not have
• Not too colored, Text under TaVRin, bright colors

```html
<!DOCTYPE html>
<html lang="en">
<head>
<meta charset="utf-8">
<title>Tavrin Gmbh – Letterhead</title>
<link href="https://fonts.googleapis.com/css2?family=Roboto:wght@400;500;700&display=swap" rel="stylesheet">
<style>
  :root {
    --backdrop: #d9d9d9;
    --paper: #f0f0f0;
    --navy: #0b1f5c;
    --steel: #8a8e99;
    --rule-grey: #b9bcc2;
    --text: #6e6e6e;
    --text-dark: #4a4a4a;
  }
  * { margin: 0; padding: 0; box-sizing: border-box; }
  html, body {
    width: 1200px; height: 1154px; overflow: hidden;
    background: var(--backdrop);
    font-family: "Roboto", Arial, sans-serif;
  }
  .letter {
    position: absolute; left: 290px; top: 140px;
    width: 621px; height: 874px;
    background: var(--paper);
    box-shadow: 0 6px 24px rgba(0,0,0,0.18);
  }
  .brand {
    position: absolute; left: 51px; top: 80px;
    display: flex; align-items: center; gap: 10px;
  }
  .brand-mark { width: 30px; height: 30px; background: var(--navy); }
  .brand-name {
    font-size: 28px; font-weight: 700; color: var(--navy);
    letter-spacing: 0.5px;
  }
  .contact {
    position: absolute; left: 479px; top: 63px;
    font-size: 10.5px; line-height: 14.5px; color: var(--text-dark);
  }
  .contact-address { margin-bottom: 3px; }
  .contact-row { display: flex; align-items: center; gap: 5px; }
  .contact-row svg { width: 10px; height: 10px; fill: var(--navy); flex: none; }
  .header-rule {
    position: absolute; left: 51px; top: 170px;
    width: 522px; height: 4px;
  }
  .header-rule .accent { position: absolute; left: 0; top: 0; width: 192px; height: 4px; background: var(--navy); }
  .header-rule .line { position: absolute; left: 192px; top: 1px; right: 0; height: 1.5px; background: var(--rule-grey); }
  .recipient {
    position: absolute; left: 54px; top: 296px;
    font-size: 11.5px; line-height: 16px; color: var(--text);
  }
  .body-copy {
    position: absolute; left: 54px; width: 515px;
    font-size: 11.5px; line-height: 16.3px; color: var(--text);
    text-align: justify;
  }
  .body-copy.first { top: 393px; }
  .body-copy.second { top: 539px; }
  .signature {
    position: absolute; left: 54px; top: 620px;
    width: 116px; height: 76px;
    background: linear-gradient(135deg, rgba(11,31,92,0.12), rgba(11,31,92,0.05));
  }
  .sign-title {
    position: absolute; left: 53px; top: 718px;
    font-size: 11.5px; color: var(--text);
  }
  .footer-band { position: absolute; left: 0; bottom: 0; width: 621px; height: 11px; }
</style>
</head>
<body>
  <main class="letter">
    <div class="brand">
      <span class="brand-mark"></span>
      <span class="brand-name">TaVRin Gmbh</span>
    </div>

    <address class="contact" style="font-style:normal">
      <div class="contact-address">Lindmattstr. 4<br>9517 Goldach</div>
      <div class="contact-row">
        <svg viewBox="0 0 10 10"><path d="M2 0.5 L3.8 2.6 L2.8 3.8 Q3.8 6 6.2 7.2 L7.4 6.2 L9.5 8 L8.4 9.5 Q4.5 9.3 0.5 1.6 Z"/></svg>
        <span>+41 71 555 01 23</span>
      </div>
      <div class="contact-row">
        <svg viewBox="0 0 10 10"><path d="M0.5 2 H9.5 V8 H0.5 Z M0.5 2 L5 5.5 L9.5 2" fill="var(--navy)" stroke="#f0f0f0" stroke-width="0.8"/></svg>
        <span>info@tavrin.ch</span>
      </div>
      <div class="contact-row">
        <svg viewBox="0 0 10 10"><circle cx="5" cy="5" r="4.5"/><path d="M0.5 5 H9.5 M5 0.5 V9.5 M5 0.5 Q2.5 5 5 9.5 M5 0.5 Q7.5 5 5 9.5" stroke="#f0f0f0" stroke-width="0.7" fill="none"/></svg>
        <span>www.tavrin.ch</span>
      </div>
    </address>

    <div class="header-rule"><span class="accent"></span><span class="line"></span></div>

    <div class="recipient">
      Dear Marlow<br>
      Northfield Print Group<br>
      Department Design
    </div>

    <p class="body-copy first">Lorem ipsum dolor sit amet, consectetuer adipiscing elit. Aenean commodo ligula eget dolor. Aenean massa. Cum sociis natoque penatibus et magnis dis parturient montes, nascetur ridiculus mus. Donec quam felis, ultricies nec, pellentesque eu, pretium quis, sem. Nulla consequat massa quis enim. Donec pede justo, fringilla vel, aliquet nec, vulputate eget, arcu. In enim justo, rhoncus ut, imperdiet a, venenatis vitae, justo. Nullam dictum felis eu pede mollis pretium. Integer tincidunt. Cras dapibus. Vivamus elementum semper nisi.Nullam dictum felis eu pede mollis pretium. Integer tincidunt. Cras dapibus. Vivamus elementum semper nisi.felis eu pede mollis pretium. Integer tincidunt. Cras dapibus.</p>

    <p class="body-copy second">Quisque rutrum. Aenean imperdiet. Etiam ultricies nisi vel augue. Curabitur ullamcorper ultricies nisi. Nam eget dui. Etiam rhoncus. Maecenas tempus, tellus eget condimentum rhoncus, sem quam semper libero, sit amet adipiscing sem neque sed ipsum.felis pede mollis pretium. I am tincidunt. Cras dapibus.</p>

    <div class="signature" role="img" aria-label="Handwritten signature of the director"></div>
    <div class="sign-title">Director/Excecutive Director</div>

    <svg class="footer-band" viewBox="0 0 621 11" preserveAspectRatio="none">
      <polygon points="0,0 376,0 385,11 0,11" fill="var(--navy)"/>
      <polygon points="381,0 621,0 621,11 390,11" fill="var(--steel)"/>
    </svg>
  </main>
</body>
</html>
```